Branding Guide and Website for Q7Systems

Need an experienced Graphics Designer with a proven track record to create a design and branding guide for all media formats. From this guide you will then create a new website design for Q7systems.com.
There will be 8 pages (to start) with the new website. Each page will have multiple features and panels each need to have individual attention and customization that collectively fit together into a single cohesive look and feel.
We have not been able to get good designs I’m attaching one version which is the best we’ve received which is not bad but needs to be polished up better and the images need to change. I’d like to have some other accent colors but not too much I like the white, dark blue, gray, dark gray style.
Here are some sites that I like –
http://www.brelvant.com/
https://www.vontaric.com/ (layout good, graphics not great)
http://www.glastrek.com/ (good layout and graphics, too much animation)
https://www.pendrowix.com/ (a little boring but the colors and some of the top images are good)
https://www.tarnowelk.com/ (a little over the top colors are off but they have some good info graphics)
We don’t expect you will code the site however if you have that capability we’ll need it responsive/flat for mobile. Otherwise we can find someone to do the programming and we’ll just need the design files and images.
Branding guide will be used for web, email, print etc. so you’ll need to consider all guidelines for all formats. That is about it let me know if any questions we can have a call to discuss further if it is easier.
Not sure why they want a minimum of 300 words I’m done now but apparently have to keep typing so that is what I’m doing and Ok I’m at 300 words, almost there and we’re here now.

Target Market(s)

Customers looking for IT Services, Private Cloud, Security Services, Advanced Support, Fully Managed or Co-Managed IT.

Industry/Entity Type

It Company

Number of Pages Required

5+ page

Font styles to use
Sans Serif

Colors
0255a3
959595
e6e6e6
ffffff

Requirements
Must have
• Clean, professional and modern look using iconography, info graphics, flat etc.

```html
<!DOCTYPE html>
<html lang="en">
<head>
<meta charset="utf-8">
<title>Q7 Systems – IT Service Excellence</title>
<link href="https://fonts.googleapis.com/css2?family=Open+Sans:wght@400;600;700;800&display=swap" rel="stylesheet">
<style>
:root{
  --blue:#0255a3;
  --blue-bright:#1e8fd9;
  --blue-soft:#5fb4ea;
  --gray:#959595;
  --gray-dark:#3a3a3a;
  --gray-light:#e6e6e6;
  --panel:#f4f4f4;
  --white:#ffffff;
  --footer:#232323;
  --footer-text:#a9a9a9;
  --yellow:#f5b800;
}
*{box-sizing:border-box;margin:0;padding:0}
html,body{width:1200px;height:2704px;overflow:hidden}
body{font-family:"Open Sans",Arial,sans-serif;color:var(--gray-dark);background:var(--white);position:relative}
.section-title{font-size:26px;font-weight:800;text-align:center;color:var(--gray-dark);letter-spacing:.5px;text-transform:uppercase}
.section-title::after{content:"";display:block;width:50px;height:3px;background:var(--blue);margin:12px auto 0}
.lead{font-size:13px;line-height:21px;color:var(--gray);text-align:center;max-width:700px;margin:0 auto}
.lead strong{color:var(--blue);font-weight:600}

/* header */
.site-header{height:88px;display:flex;align-items:center;justify-content:space-between;padding:0 40px;background:var(--white);border-bottom:1px solid var(--gray-light)}
.brand{display:flex;align-items:center;gap:10px;font-size:26px;font-weight:800;color:var(--blue)}
.brand-mark{width:22px;height:22px;background:var(--blue)}
.main-nav{display:flex;gap:2px}
.main-nav a{font-size:11px;font-weight:600;color:var(--gray);text-decoration:none;text-transform:uppercase;padding:10px 14px;letter-spacing:.3px}
.main-nav a.is-active{color:var(--white);background:var(--blue)}

/* hero */
.hero{position:relative;height:512px;background:linear-gradient(135deg,var(--blue-bright),var(--blue));overflow:hidden}
.hero-art{position:absolute;left:560px;top:40px;width:580px;height:420px;border-radius:210px;background:radial-gradient(ellipse at center,rgba(255,255,255,.85),rgba(255,255,255,.35) 60%,rgba(255,255,255,0) 75%)}
.hero-copy{position:absolute;left:40px;top:268px}
.hero-title{font-size:40px;font-weight:800;color:var(--white);letter-spacing:.5px}
.hero-sub{font-size:14px;color:#d9ecfb;margin-top:6px}
.btn{display:inline-block;font-size:11px;font-weight:700;text-transform:uppercase;text-decoration:none;letter-spacing:.5px}
.btn-hero{margin-top:36px;background:var(--yellow);color:var(--white);padding:14px 26px}
.hero-arrow{position:absolute;top:280px;width:36px;height:70px;background:rgba(2,60,120,.75);display:flex;align-items:center;justify-content:center}
.hero-arrow.prev{left:0}.hero-arrow.next{right:0}

/* services */
.services{height:480px;background:var(--panel);padding-top:50px}
.services .lead{margin-top:20px;width:440px}
.service-grid{display:grid;grid-template-columns:repeat(3,300px);column-gap:50px;row-gap:44px;width:1000px;margin:50px auto 0}
.service{display:flex;gap:18px}
.service svg{flex:0 0 40px}
.service h3{font-size:16px;font-weight:600;color:var(--gray-dark);margin-bottom:6px}
.service p{font-size:11.5px;line-height:18px;color:var(--gray)}

/* help */
.help{height:640px;padding-top:86px}
.help .lead{margin-top:22px}
.help-grid{display:grid;grid-template-columns:repeat(4,240px);column-gap:40px;width:1080px;margin:36px auto 0}
.help-photo{height:124px}
.help-card h3{font-size:16px;font-weight:600;text-align:center;margin-top:22px;color:var(--gray-dark)}
.help-card p{font-size:11.5px;line-height:18px;color:var(--gray);text-align:center;margin-top:6px}
.help .note{margin-top:40px;max-width:620px;font-size:12px}
.client-row{display:flex;justify-content:space-between;width:820px;margin:40px auto 0;align-items:center}
.client{font-size:24px;font-weight:700;color:#8a8a8a;display:flex;align-items:center;gap:8px}
.client-dot{width:18px;height:18px;border-radius:50%;background:#8a8a8a}

/* testimonials */
.testimonials{height:360px;background:var(--panel);padding-top:36px}
.quote-grid{display:grid;grid-template-columns:repeat(3,300px);column-gap:60px;width:1020px;margin:46px auto 0}
.quote p{font-size:12px;line-height:20px;font-style:normal;color:var(--gray);text-align:center}
.quote cite{display:block;font-style:normal;font-size:12px;color:var(--blue);text-align:center;margin-top:14px;font-weight:600}

/* different */
.different{position:relative;height:340px;padding-top:62px}
.different .lead{margin-top:22px;max-width:640px}
.different-art{position:absolute;right:40px;top:0;width:190px;height:340px;background:linear-gradient(180deg,#f3f7fb,#dfe9f3)}
.btn-primary{display:block;width:160px;margin:36px auto 0;background:var(--blue);color:var(--white);text-align:center;padding:14px 0}

/* footer */
.site-footer{height:284px;background:var(--footer);padding:44px 40px 0;display:grid;grid-template-columns:280px 260px 300px 1fr;column-gap:40px;position:relative}
.social{display:flex;gap:8px;margin-bottom:18px}
.social span{width:28px;height:28px;border-radius:50%;border:1px solid var(--footer-text)}
.site-footer h4{font-size:16px;font-weight:600;color:var(--white);margin-bottom:18px}
.site-footer p,.site-footer li{font-size:11px;line-height:19px;color:var(--footer-text);list-style:none}
.field{width:200px;height:30px;background:var(--white);margin-bottom:10px;font-size:11px;color:var(--gray);padding:7px 10px}
.btn-submit{background:var(--blue);color:var(--white);padding:9px 18px}
.browse li::before{content:"";display:inline-block;width:5px;height:5px;background:var(--blue-soft);margin-right:8px;vertical-align:middle}
.to-top{position:absolute;right:20px;bottom:20px;width:28px;height:28px;background:#3a3a3a;display:flex;align-items:center;justify-content:center}
</style>
</head>
<body>

<header class="site-header">
  <div class="brand"><span class="brand-mark"></span>Q7 Systems</div>
  <nav class="main-nav">
    <a class="is-active" href="#">Home</a>
    <a href="#">Managed Services</a>
    <a href="#">Corporate Cloud</a>
    <a href="#">Cloud Solutions</a>
    <a href="#">Managed Security</a>
    <a href="#">Services</a>
    <a href="#">Company</a>
  </nav>
</header>

<section class="hero">
  <div class="hero-art" role="img" aria-label="Illustration of a cloud linking servers, laptops and desktop computers"></div>
  <div class="hero-copy">
    <h1 class="hero-title">IT SERVICE EXCELLENCE</h1>
    <p class="hero-sub">Striving for Continuous Service Improvement for our Clients</p>
    <a class="btn btn-hero" href="#">Get Started Now</a>
  </div>
  <div class="hero-arrow prev"><svg width="12" height="20" viewBox="0 0 12 20"><path d="M10 2 2 10l8 8" fill="none" stroke="#fff" stroke-width="2.5"/></svg></div>
  <div class="hero-arrow next"><svg width="12" height="20" viewBox="0 0 12 20"><path d="M2 2l8 8-8 8" fill="none" stroke="#fff" stroke-width="2.5"/></svg></div>
</section>

<section class="services">
  <h2 class="section-title">What We Do</h2>
  <p class="lead">Providing <strong>With Care</strong> IT service to dedicated businesses across every industry, keeping their systems fast, safe and up.</p>
  <div class="service-grid">
    <div class="service">
      <svg width="40" height="40" viewBox="0 0 40 40" fill="none" stroke="#959595" stroke-width="2"><circle cx="20" cy="20" r="6"/><path d="M20 4v6M20 30v6M4 20h6M30 20h6M9 9l4 4M27 27l4 4M9 31l4-4M27 13l4-4"/></svg>
      <div><h3>Managed Services</h3><p>We provide comprehensive technology management, IT solutions and support, whether you need a full team or a partner.</p></div>
    </div>
    <div class="service">
      <svg width="40" height="40" viewBox="0 0 40 40" fill="none" stroke="#959595" stroke-width="2"><path d="M11 30h19a7 7 0 0 0 0-14 10 10 0 0 0-19 2 6 6 0 0 0 0 12z"/></svg>
      <div><h3>Private Cloud</h3><p>We set up servers and applications on our cloud so yours run with predictable performance and dependable access.</p></div>
    </div>
    <div class="service">
      <svg width="40" height="40" viewBox="0 0 40 40" fill="none" stroke="#959595" stroke-width="2"><path d="M20 4 7 9v10c0 8 6 14 13 17 7-3 13-9 13-17V9z"/><path d="m14 20 4 4 8-8"/></svg>
      <div><h3>Security Services</h3><p>To protect networks and systems, we watch traffic, patch and test your defenses in real time before threats arrive.</p></div>
    </div>
    <div class="service">
      <svg width="40" height="40" viewBox="0 0 40 40" fill="none" stroke="#959595" stroke-width="2"><circle cx="20" cy="13" r="7"/><path d="M7 36c0-8 6-12 13-12s13 4 13 12"/></svg>
      <div><h3>Advanced Support</h3><p>Talk to experienced engineers who know your setup, with clear answers and quick fixes whenever your team needs them.</p></div>
    </div>
    <div class="service">
      <svg width="40" height="40" viewBox="0 0 40 40" fill="none" stroke="#959595" stroke-width="2"><rect x="15" y="4" width="10" height="8"/><rect x="4" y="28" width="10" height="8"/><rect x="26" y="28" width="10" height="8"/><path d="M20 12v8M9 28v-8h22v8"/></svg>
      <div><h3>Network Services</h3><p>Every organization needs a working network. We design, install and maintain wired and wireless links that scale.</p></div>
    </div>
    <div class="service">
      <svg width="40" height="40" viewBox="0 0 40 40" fill="none" stroke="#959595" stroke-width="2"><path d="M32 20a12 12 0 1 1-4-9"/><path d="M29 4v7h-7"/></svg>
      <div><h3>Disaster Recovery</h3><p>Backup plans that restore data quickly so a failure, outage or breach never brings your business to a stop.</p></div>
    </div>
  </div>
</section>

<section class="help">
  <h2 class="section-title">How Can We Help Your Business?</h2>
  <p class="lead">Our complete manage service quests to our ability to <strong>provide complete end-to-end technology</strong> management solutions, allowing your teams to focus on growth while we handle the rest.</p>
  <div class="help-grid">
    <div class="help-card">
      <div class="help-photo" role="img" aria-label="Photo of glowing network connections" style="background:linear-gradient(135deg,#2a6fb8,#7fc1ec)"></div>
      <h3>Your Network</h3><p>Consistent reliable availability, constant management, smaller failures.</p>
    </div>
    <div class="help-card">
      <div class="help-photo" role="img" aria-label="Photo of a digital security lock" style="background:linear-gradient(135deg,#1b2b4a,#a13a4a)"></div>
      <h3>Your Web Presence</h3><p>A trusted site your clients reach through the smoothest of journeys.</p>
    </div>
    <div class="help-card">
      <div class="help-photo" role="img" aria-label="Photo of rows of server racks" style="background:linear-gradient(135deg,#3b3b3b,#9a9a9a)"></div>
      <h3>Your Applications</h3><p>Software shaped to your needs and run on the cloud of your choice.</p>
    </div>
    <div class="help-card">
      <div class="help-photo" role="img" aria-label="Photo of an engineer working in a data center" style="background:linear-gradient(135deg,#2c3e50,#8fa4b8)"></div>
      <h3>Your Piece of Mind</h3><p>Rest easy knowing your systems are watched by a dedicated team.</p>
    </div>
  </div>
  <p class="lead note">With trusted partners and tools we help businesses of every size stay ahead, working with brands like <strong>these</strong> every day.</p>
  <div class="client-row">
    <span class="client"><span class="client-dot"></span>Lumora</span>
    <span class="client">Veltrix</span>
    <span class="client">Pictavo</span>
    <span class="client">stillbank</span>
    <span class="client">Tessel</span>
  </div>
</section>

<section class="testimonials">
  <h2 class="section-title">What Are People Saying About Q7 Systems</h2>
  <div class="quote-grid">
    <blockquote class="quote"><p>“Since switching our support to this team our systems run smoother than ever, problems are solved before we notice them and our staff can finally focus on clients.”</p><cite>Dana Reyes, City Name</cite></blockquote>
    <blockquote class="quote"><p>“Moving to their private cloud was painless. The planning was clear, the cutover was quick and we have not had a single outage since the project was completed.”</p><cite>Dana Reyes, City Name</cite></blockquote>
    <blockquote class="quote"><p>“Responsive, honest and knowledgeable. They treat our network like their own and always explain what they are doing in plain terms our team understands.”</p><cite>Dana Reyes, City Name</cite></blockquote>
  </div>
</section>

<section class="different">
  <h2 class="section-title">We Are Different</h2>
  <p class="lead">We put people first and treat every client like a long term partner. Our engineers listen, plan and act with care, delivering technology that fits the way you work, with clear pricing and no surprises along the way.</p>
  <a class="btn btn-primary" href="#">How It Works</a>
  <div class="different-art" role="img" aria-label="Illustration of a friendly IT consultant"></div>
</section>

<footer class="site-footer">
  <div>
    <div class="social"><span></span><span></span><span></span><span></span></div>
    <p>© 2024 Q7 Systems, Inc.</p>
    <p>All Rights Reserved</p>
    <p>Privacy Policy</p>
  </div>
  <div>
    <h4>Contact us</h4>
    <p>1470 Harbor Point Dr, Suite 210</p>
    <p>Fairview, CA 90210</p>
    <p>1 (555) 014-7230</p>
    <p>hello@q7systems.com</p>
  </div>
  <div>
    <h4>Newsletter</h4>
    <div class="field">Name</div>
    <div class="field">Email address</div>
    <a class="btn btn-submit" href="#">Submit</a>
  </div>
  <div class="browse">
    <h4>Browse</h4>
    <ul>
      <li>Managed Services</li>
      <li>IT Private Cloud</li>
      <li>Security Services</li>
      <li>Advanced Support</li>
      <li>Network Services</li>
      <li>Disaster Recovery</li>
    </ul>
  </div>
  <div class="to-top"><svg width="12" height="8" viewBox="0 0 12 8"><path d="M1 7l5-5 5 5" fill="none" stroke="#fff" stroke-width="2"/></svg></div>
</footer>

</body>
</html>
```